CREATE A KILLER WEBSITE DESIGN

We are a firearms training company that trains CIVILIANS (no police or military pictures - thank you!) to defend themselves and are looking for a killer design that's clean, easy to navigate and modern! We want the newest trends applied to this sight like a scrollable site so you can scroll down and see all the features. We are okay with tweaking the HTML but need the artistic design to look good. I'll provide a link to our current site along with a sight we really like so you can get an idea!

I'm supplying a PowerPoint Design we are going with from another designer so you can match the style to the new site.

PAGES: (Please use information from our current site. We like the information but just want a more polished look similar to the NWDPA site below but in our colors.)
Home - Long Form Scrolling Site. Top fold will be a video with a play button.
Harbor Institute - Seven Level Training Program Info Page That Will Contain A Video.
Contact Us - This will be a page that DOES NOT CONTAIN AN EMAIL ADDRESS. Just a contact us form
Meet The Trainer: Dennis Pollock

Our site:
https://www.brightmeadowskills.biz

Sights We Like:
https://www.nwdefenseplanners.com
https://quorvel.com
https://lindenplatecorp.com
https://www.velbrookgear.com

Target Market(s)

Men and women ages 21 to 100 years old

Industry/Entity Type

Self Defense

Number of Pages Required

5+ page

Font styles to use
Sans Serif

Colors
f26267

Requirements
Must have
• Clean and engaging. Use of colors that match our logo.
Should not have
• Poor design quality

```html
<!DOCTYPE html>
<html lang="en">
<head>
<meta charset="utf-8">
<title>Brightmeadow Skills – Hands On Training</title>
<link rel="stylesheet" href="https://fonts.googleapis.com/css2?family=Montserrat:wght@400;500;600;700&family=Open+Sans:wght@700;800&display=swap">
<style>
:root{
  --red:#e31e24;
  --red-deep:#8e0d10;
  --ink:#141414;
  --coal:#1c1c1c;
  --slate:#4a4a4a;
  --paper:#ffffff;
  --mist:#cfcfcf;
  --body:#333333;
}
*{box-sizing:border-box;margin:0;padding:0}
html,body{width:1200px;height:3605px;overflow:hidden}
body{position:relative;background:var(--paper);font-family:'Montserrat',sans-serif;color:var(--body)}
.backdrop-band{position:absolute;left:0;top:0;width:1200px;height:666px;background:var(--red)}
.section{position:absolute;left:76px;width:1047px;overflow:hidden}
.abs{position:absolute}
.btn{position:absolute;display:flex;align-items:center;justify-content:center;font-size:10px;font-weight:600;border-radius:2px}
.btn-red{background:var(--red);color:#fff}
.btn-white{background:#fff;color:var(--ink)}
.accent{color:var(--red)}
.photo{position:absolute}
.play{position:absolute}

/* hero */
.hero{top:80px;height:586px;background:radial-gradient(circle at 60% 40%,#2b2b2b,#0d0d0d 75%);clip-path:polygon(0 0,100% 0,100% 536px,50% 586px,0 536px)}
.top-links{left:176px;top:20px;display:flex;gap:18px;font-size:9px;color:#ddd}
.social-top{left:771px;top:18px;display:flex;gap:10px;font-size:9px;color:#fff;font-weight:600}
.brand{left:176px;top:64px;font-size:12px;font-weight:700;color:var(--red);letter-spacing:.2px}
.nav{left:394px;top:64px;display:flex;gap:25px;font-size:11px;color:#eee}
.hero-title{left:176px;top:190px;font-family:'Open Sans',sans-serif;font-weight:800;font-size:58px;line-height:62px;color:#fff;letter-spacing:1px}
.hero-sub{left:176px;top:328px;width:350px;font-size:10.5px;line-height:12px;color:#fff}
.hero-photo{left:500px;top:110px;width:420px;height:450px;background:radial-gradient(ellipse at 50% 45%,#3a3a3a,#151515 70%,transparent 72%)}

/* about */
.about{top:666px;height:444px;background:var(--paper)}
.about-photo{left:176px;top:59px;width:326px;height:329px;background:linear-gradient(135deg,#6f7f4e,#b4a98f 55%,#2a6fd0);clip-path:polygon(0 0,100% 0,88% 100%,0 100%)}
.about-edge{left:176px;top:59px;width:333px;height:329px;background:var(--red);clip-path:polygon(98% 0,100% 0,90% 100%,88% 100%)}
.about-title{left:575px;top:63px;font-size:19px;font-weight:500;color:var(--ink)}
.about-title b{color:var(--red);font-weight:700}
.about-copy{left:572px;top:96px;width:318px;font-size:9.6px;line-height:13.2px;color:var(--body)}
.about-copy p+p{margin-top:12px}

/* levels intro */
.levels-intro{top:1110px;height:251px;background:var(--slate);text-align:center;color:#fff}
.levels-intro h2{position:absolute;left:0;right:0;top:34px;font-weight:500;font-size:19px;line-height:24px}
.levels-intro h2 span{display:block;color:var(--red)}
.levels-intro .copy{position:absolute;left:232px;width:612px;font-size:9.8px;line-height:12.4px}

/* levels grid */
.levels{top:1361px;height:337px;background:linear-gradient(90deg,#1a1a1a,#2a1212)}
.levels-slash{left:0;top:0;width:1047px;height:337px;background:linear-gradient(90deg,var(--red-deep),var(--red));clip-path:polygon(62% 0,100% 0,100% 100%,18% 100%)}
.level{position:absolute;height:84px;display:flex;align-items:center}
.level-num{font-family:'Open Sans',sans-serif;font-weight:800;font-size:70px;line-height:84px;color:var(--ink);-webkit-text-stroke:2px var(--red);width:40px}
.level-card{width:110px;height:84px;background:#fff;clip-path:polygon(0 0,100% 0,100% 100%,0 100%,14px 50%);display:flex;flex-direction:column;align-items:center;justify-content:center;text-align:center;font-size:12px;line-height:13px;color:var(--ink);padding-left:10px}
.level-card svg{margin-bottom:3px}

/* video */
.video{top:1698px;height:426px;background:var(--paper)}
.video-frame{left:176px;top:59px;width:697px;height:280px;background:linear-gradient(100deg,#2d2d2d,#6b4036 35%,#2b6a70 70%,#0f1e2a)}

/* services */
.services{top:2124px;height:397px;background:linear-gradient(120deg,#2a0c0c,#6d1214 55%,#1a1a1a)}
.services-title{left:176px;top:48px;font-size:20px;font-weight:500;color:#fff}
.services-title b{color:var(--red);font-weight:700}
.toggle{left:712px;top:46px;width:160px;height:31px;display:flex;font-size:11px;font-weight:700}
.toggle span{flex:1;display:flex;align-items:center;justify-content:center}
.toggle .on{background:var(--red);color:#fff;clip-path:polygon(0 0,100% 0,88% 100%,0 100%);margin-right:-10px}
.toggle .off{background:#fff;color:var(--ink)}
.service{position:absolute;top:112px;width:227px}
.service-img{height:175px;position:relative}
.tag{position:absolute;left:24px;bottom:12px;background:#fff;color:var(--ink);font-size:7px;font-weight:600;padding:3px 10px;border-radius:8px}
.service h3{margin-top:17px;font-size:14px;font-weight:700;color:#fff}
.service p{margin-top:9px;font-size:9px;line-height:14px;color:#e6e6e6}

/* as seen on */
.seen{top:2521px;height:282px;background:var(--paper)}
.seen h2{position:absolute;left:0;right:0;top:46px;text-align:center;font-size:20px;font-weight:500;color:var(--ink)}
.seen h2 b{color:var(--red);font-weight:700}
.outlet{position:absolute;top:126px;width:110px;height:110px;border:3px solid var(--red);border-radius:50%;display:flex;align-items:center;justify-content:center;text-align:center;font-size:14px;font-weight:700;color:var(--ink);line-height:16px}

/* contact */
.contact{top:2803px;height:351px;background:radial-gradient(circle at 50% 40%,#2a2a2a,#121212 70%)}
.corner{top:0;width:95px;height:95px;background:var(--red)}
.corner-left{left:0;clip-path:polygon(0 0,100% 0,0 100%)}
.corner-right{right:0;clip-path:polygon(0 0,100% 0,100% 100%)}
.contact h2{position:absolute;left:0;right:0;top:30px;text-align:center;font-size:19px;font-weight:500;color:#fff}
.contact h2 b{color:var(--red);font-weight:700}
.field{position:absolute;border:1px solid #8a8a8a;font-size:9px;color:#ddd;padding:9px 12px}

/* footer */
.footer{top:3154px;height:280px;background:#0b0b0b;color:#ddd}
.footer-brand{left:179px;top:44px;width:190px;font-size:16px;line-height:20px;font-weight:700;color:var(--red)}
.footer-tag{left:386px;top:44px;width:440px;font-size:9px;line-height:12px}
.contact-list{left:176px;top:148px;font-size:9.5px;line-height:13px}
.contact-list li{list-style:none;display:flex;align-items:center;gap:12px;height:25px}
.contact-list svg{flex:none}
.newsletter{left:386px;top:124px;width:330px;font-size:9px;line-height:11px}
.news-input{left:386px;top:174px;width:231px;height:29px;background:#fff;color:#777;font-size:9px;padding:9px 18px}
.news-submit{left:624px;top:174px;width:84px;height:29px}
.copyright{left:386px;top:223px;font-size:9px}
.social-foot{left:761px;top:122px;display:flex;gap:6px}
.social-foot span{width:24px;height:24px;border:1px solid #ccc;display:flex;align-items:center;justify-content:center;font-size:7px}
</style>
</head>
<body>
<div class="backdrop-band"></div>

<header class="section hero">
  <div class="photo hero-photo" role="img" aria-label="Hero video: trainee in cap and ear protection aiming at the range"></div>
  <svg class="play" style="left:679px;top:304px" width="62" height="62" viewBox="0 0 62 62" aria-label="Play video"><circle cx="31" cy="31" r="28" fill="rgba(0,0,0,.35)" stroke="#fff" stroke-width="4"/><path d="M25 19l18 12-18 12z" fill="#fff"/></svg>
  <nav class="abs top-links"><span>Harbor Institute</span><span>Testimonial</span><span>Lost Certificate</span></nav>
  <div class="abs social-top"><span>Kite</span><span>Folio</span><span>Orbit</span><span>Linkwork</span></div>
  <div class="abs brand">BRIGHTMEADOW SKILLS</div>
  <nav class="abs nav"><span>Home</span><span>About</span><span>Upcoming Classes</span><span>Shop</span><span>Videos</span></nav>
  <a class="btn btn-red" style="left:761px;top:59px;width:112px;height:28px">Get Tickets Now</a>
  <h1 class="abs hero-title">HAND ON<br><span class="accent">TRAINING</span></h1>
  <p class="abs hero-sub">Your Life may depend on ehat you learbn in your concealed carry training&nbsp; -dont settle for a gun shop closs</p>
  <a class="btn btn-white" style="left:176px;top:376px;width:111px;height:28px">Harbor Institute</a>
  <a class="btn btn-red" style="left:299px;top:376px;width:111px;height:28px">Get Tickets Now</a>
</header>

<section class="section about">
  <div class="abs about-edge"></div>
  <div class="photo about-photo" role="img" aria-label="Two students practising pistol stance outdoors with a shot target card"></div>
  <h2 class="abs about-title">ABOUT <b>THE INSTRUCTOR</b></h2>
  <div class="abs about-copy">
    <p>Dennis Pollock is a 3rd generation Jacksonville native and delighted to be a part of this great community.&nbsp; He is a true security expert with 25 years of experience in the security industry.&nbsp; He has appeared on national news outlets.&nbsp; He has been Featured in numerous publications and has trained thousands to protect themselves and their homes from thugs and thieves. He is certified by both the NMSA &amp; the NWDPA as a firearms instructor.&nbsp; He is also an NMSA Range Safety Officer and Defensive Pistol Instructor.&nbsp; He often says: "My students are like family so I take their security personal.&nbsp; I want them to feel confident that they can protect themselves and their families!"</p>
    <p>Brightmeadow Skills is a radically different concealed carry class focusing on the TRUTH about how "Real Attacks" take place.&nbsp; The Concealed Carry Class goes over way more than just the boring, lecture-style, gun shop curriculum into real strategies, tactics and training suggestions to help you prepare!&nbsp; You have to experience it to believe it!</p>
  </div>
  <a class="btn btn-red" style="left:571px;top:360px;width:111px;height:28px">Get Tickets Now</a>
</section>

<section class="section levels-intro">
  <h2>OUR 7 LEVELS OF TRAINING<span>TAKE YOU FROM ZERO TO HERO</span></h2>
  <p class="copy" style="top:101px">Wanna hear something funny?&nbsp; Guess what the average person asks about a concealed weapons class?&nbsp; "How much is it and how long is it?"&nbsp; Can you believe it?&nbsp; We are talking about preparing you for life and death situations and the main concern is "How Fast" and "How Cheap?"&nbsp; WOW!</p>
  <p class="copy" style="top:152px">Why do most people settle for a cheap &amp; quick concealed carry class?&nbsp; It's a fair question!&nbsp; Could you imagine a military soldier trained by a 2-hour class?&nbsp; How effective would they be in the heat of battle?&nbsp; If you want to be ready to SURVIVE an attack, YOU NEED MORE than a basic, run of the mill class!&nbsp; That's why we created a PROPRIETARY 7 LEVEL TRAINING SYSTEM to take you all the way to the peak of readiness!</p>
</section>

<section class="section levels">
  <div class="abs levels-slash"></div>
  <div class="level" style="left:176px;top:70px"><span class="level-num">1</span><div class="level-card"><svg width="22" height="16" viewBox="0 0 22 16"><path d="M1 2h19v5H9l-2 8H3l2-8H1z" fill="none" stroke="#141414" stroke-width="1.5"/></svg>Conceled<br>Carry Class</div></div>
  <div class="level" style="left:363px;top:70px"><span class="level-num">2</span><div class="level-card"><svg width="18" height="18" viewBox="0 0 18 18"><circle cx="9" cy="9" r="8" fill="none" stroke="#141414" stroke-width="1.5"/><circle cx="9" cy="9" r="4" fill="none" stroke="#141414" stroke-width="1.5"/><circle cx="9" cy="9" r="1.5" fill="#141414"/></svg>Dynamic<br>defencive<br>shooting</div></div>
  <div class="level" style="left:540px;top:70px"><span class="level-num">3</span><div class="level-card"><svg width="18" height="18" viewBox="0 0 18 18"><circle cx="9" cy="9" r="7" fill="none" stroke="#141414" stroke-width="1.5"/><path d="M9 2v14M2 9h14" stroke="#141414" stroke-width="1.2"/></svg>Fine tuning<br>your technicque</div></div>
  <div class="level" style="left:722px;top:70px"><span class="level-num">4</span><div class="level-card"><svg width="20" height="18" viewBox="0 0 20 18"><rect x="1" y="3" width="18" height="11" rx="5" fill="none" stroke="#141414" stroke-width="1.5"/><circle cx="7" cy="9" r="2" fill="#141414"/><circle cx="13" cy="9" r="2" fill="#141414"/></svg>Virtual<br>threat - Lab</div></div>
  <div class="level" style="left:281px;top:187px"><span class="level-num">5</span><div class="level-card"><svg width="18" height="18" viewBox="0 0 18 18"><circle cx="9" cy="9" r="7" fill="none" stroke="#141414" stroke-width="1.5"/><circle cx="9" cy="9" r="3" fill="none" stroke="#141414" stroke-width="1.5"/></svg>Tactical skills<br>&amp; drills</div></div>
  <div class="level" style="left:470px;top:187px"><span class="level-num">6</span><div class="level-card"><svg width="20" height="18" viewBox="0 0 20 18"><path d="M2 7L10 2l8 5M4 8v8M8 8v8M12 8v8M16 8v8M2 17h16" fill="none" stroke="#141414" stroke-width="1.5"/></svg>Close quaters<br>defense</div></div>
  <div class="level" style="left:652px;top:187px"><span class="level-num">7</span><div class="level-card"><svg width="26" height="18" viewBox="0 0 26 18"><path d="M4 2v12h6" fill="none" stroke="#141414" stroke-width="1.5"/><rect x="13" y="2" width="12" height="7" fill="none" stroke="#141414"/><text x="19" y="7.5" font-size="5" text-anchor="middle" fill="#141414" font-family="Montserrat,sans-serif">LIVE</text></svg>Live scenario<br>threat-lab</div></div>
</section>

<section class="section video">
  <div class="photo video-frame" role="img" aria-label="Trainee aiming at a projected virtual target screen in the training lab"></div>
  <svg class="abs" style="left:493px;top:167px" width="62" height="62" viewBox="0 0 62 62"><circle cx="31" cy="31" r="28" fill="rgba(0,0,0,.35)" stroke="#fff" stroke-width="4"/><path d="M25 19l18 12-18 12z" fill="#fff"/></svg>
  <a class="btn btn-red" style="left:455px;top:357px;width:137px;height:30px">Click Here Learn More</a>
</section>

<section class="section services">
  <h2 class="abs services-title">Our <b>Services</b></h2>
  <div class="abs toggle"><span class="on">By Class</span><span class="off">By Date</span></div>
  <article class="service" style="left:176px">
    <div class="service-img" role="img" aria-label="Pistol in a belt holster" style="background:linear-gradient(135deg,#3a3a3a,#111 60%,#5b6b86)"><span class="tag">NEWS</span></div>
    <h3>He made the first step!</h3>
    <p>Lorem ipsum dolor sit amet, and consectetur adipiscing elit sed do eiusmod</p>
  </article>
  <article class="service" style="left:413px">
    <div class="service-img" role="img" aria-label="Instructor coaching a student with a training pistol" style="background:linear-gradient(135deg,#4a4a52,#2a2a30 50%,#8a7a6a)"><span class="tag">TIPS</span></div>
    <h3>He made the first step!</h3>
    <p>Lorem ipsum dolor sit amet, and consectetur adipiscing elit sed do eiusmod</p>
  </article>
  <article class="service" style="left:650px">
    <div class="service-img" role="img" aria-label="Ear protection muffs on a shooting range bench" style="background:linear-gradient(180deg,#7a4a2a,#c9864a 40%,#3a1a14)"><span class="tag">BOOKS</span></div>
    <h3>He made the first step!</h3>
    <p>Lorem ipsum dolor sit amet, and consectetur adipiscing elit sed do eiusmod</p>
  </article>
</section>

<section class="section seen">
  <h2>AS <b>SEEN ON</b></h2>
  <div class="outlet" style="left:177px">Crestline<br>News</div>
  <div class="outlet" style="left:372px">Harbor TV</div>
  <div class="outlet" style="left:568px">Summit One</div>
  <div class="outlet" style="left:762px">Pinewood</div>
</section>

<section class="section contact">
  <div class="abs corner corner-left"></div>
  <div class="abs corner corner-right"></div>
  <h2>GET <b>IN TOUCH</b></h2>
  <div class="field" style="left:281px;top:78px;width:238px;height:31px">First name</div>
  <div class="field" style="left:526px;top:78px;width:238px;height:31px">Last Name</div>
  <div class="field" style="left:281px;top:119px;width:483px;height:31px">Email Id</div>
  <div class="field" style="left:281px;top:159px;width:483px;height:90px">Message</div>
  <a class="btn btn-red" style="left:460px;top:280px;width:126px;height:33px;font-size:12px">Submit Now</a>
</section>

<footer class="section footer">
  <div class="abs footer-brand">BRIGHTMEADOW<br>SKILLS</div>
  <p class="abs footer-tag">NMSA FIREARMS INSTRUCTOR, NWDPA INSTRUCTOR &amp; TRAINING COUNSELLOR, NEWS CORRESPONDENT, AND SECURITY EXPERT</p>
  <ul class="abs contact-list">
    <li><svg width="12" height="14" viewBox="0 0 12 14"><path d="M6 13S1 8 1 5a5 5 0 0110 0c0 3-5 8-5 8z" fill="none" stroke="#fff" stroke-width="1.4"/><circle cx="6" cy="5" r="1.8" fill="#fff"/></svg>P.O. Box 4412</li>
    <li style="padding-left:24px">Cedar Point, FL 32099</li>
    <li><svg width="12" height="12" viewBox="0 0 12 12"><path d="M2 1l3 3-1.5 1.5a7 7 0 003 3L8 7l3 3-2 2C5 12 0 7 0 3z" fill="#fff"/></svg>000 0000 0000</li>
    <li><svg width="12" height="10" viewBox="0 0 12 10"><rect x=".7" y=".7" width="10.6" height="8.6" fill="none" stroke="#fff" stroke-width="1.2"/><path d="M1 1l5 4 5-4" fill="none" stroke="#fff" stroke-width="1.2"/></svg>info@brightmeadowmail.com</li>
  </ul>
  <div class="abs newsletter"><p>Subscribe The Newsletter</p><p style="margin-top:7px">Subscribe to our newsletter and stay updated on the latest news. We will keep you&nbsp; informed about special offers.</p></div>
  <div class="abs news-input">Email Address*</div>
  <a class="btn btn-red news-submit">Submit</a>
  <p class="abs copyright">©2020 Copyright Brightmeadow Skills , All rights reserved</p>
  <div class="abs social-foot"><span>Kite</span><span>Folio</span><span>Orbit</span><span>Link</span></div>
</footer>
</body>
</html>
```